Business Card Design Project

We are not a new company, but renamed to "Vantorin Kitchens" last year. We specialize in modern high-end cabinetry imports. We would like to communicate a sense of quality and cutting edge technology. Ideally the design would incorporate our logo colors, silver, red and preferably a black, matte background. Though we are open to suggestions.
Logo is attached.
Edit: I have attached rough drafts of the previous cards, this way you will have all necessary content that needs to go on the cards.
Updates
Project Deadline Extended
Reason: We have received a lot of great designs, but due to the sheer number we couldn't respond to all. We will extend the deadline for another 7 days to finalize and provide feedback to designers.
Thank you for your hard work!
Industry/Entity Type
Business
Look and feel
Each slider illustrates characteristics of the customer's brand and the style your logo design should communicate.

```html
<!DOCTYPE html>
<html lang="en">
<head>
<meta charset="utf-8">
<title>Vantorin Kitchens – Business Card</title>
<link href="https://fonts.googleapis.com/css2?family=Arimo:wght@400;700&display=swap" rel="stylesheet">
<style>
  :root {
    --page: #b9c9c7;
    --card-dark: #2a2a2b;
    --card-mid: #3c3c3e;
    --silver: #a9a9ab;
    --silver-light: #d4d4d6;
    --panel-grey: #8e8e90;
    --accent-red: #e3202a;
    --text-white: #f2f2f2;
  }
  * { margin: 0; padding: 0; box-sizing: border-box; }
  html, body {
    width: 1200px; height: 973px; overflow: hidden;
    background: var(--page);
    font-family: "Arimo", Arial, sans-serif;
  }
  .sheet {
    width: 1200px; height: 973px;
    display: flex; flex-direction: column; align-items: center; justify-content: center;
    gap: 40px;
  }
  .card {
    position: relative;
    width: 700px; height: 400px;
    overflow: hidden;
    background: linear-gradient(160deg, var(--card-mid) 0%, var(--card-dark) 55%, #1f1f20 100%);
    box-shadow: 0 6px 18px rgba(0,0,0,0.25);
  }
  .card-art { position: absolute; inset: 0; }

  /* front */
  .brand {
    position: absolute; left: 56px; top: 66px;
    display: flex; align-items: center; gap: 12px;
  }
  .brand-mark { width: 20px; height: 20px; background: var(--silver); flex: none; }
  .brand-name {
    font-size: 27px; font-weight: 700; letter-spacing: 1.5px;
    text-transform: uppercase; color: var(--silver-light);
    white-space: nowrap;
  }
  .holder {
    position: absolute; left: 70px; top: 190px;
    font-size: 18px; font-weight: 700; color: var(--text-white);
    letter-spacing: 0.5px;
  }
  .holder-role { color: var(--accent-red); font-weight: 400; font-size: 16px; }
  .address {
    position: absolute; left: 85px; top: 234px;
    font-size: 16px; line-height: 1.35; color: var(--text-white);
  }
  .contacts {
    position: absolute; right: 30px; top: 96px;
    list-style: none;
    font-size: 14px; line-height: 23px; color: var(--text-white);
  }
  .contacts li { display: flex; align-items: center; gap: 6px; }
  .contact-web { padding-left: 19px; }
  .contact-email {
    position: absolute; left: 420px; top: 262px;
    font-size: 14px; color: var(--text-white);
    display: flex; align-items: center; gap: 6px;
  }
  .icon { width: 13px; height: 13px; flex: none; }

  /* back */
  .back-brand {
    position: absolute; inset: 0;
    display: flex; align-items: center; justify-content: center; gap: 20px;
  }
  .back-brand .brand-mark { width: 36px; height: 36px; }
  .back-brand .brand-name { font-size: 46px; color: var(--silver); }
</style>
</head>
<body>
<main class="sheet">

  <section class="card card-front" aria-label="Business card front">
    <svg class="card-art" viewBox="0 0 700 400" aria-hidden="true">
      <path d="M160 400 C380 390 400 90 700 20 L700 400 Z" fill="var(--panel-grey)"/>
      <path d="M60 400 C320 392 350 70 700 0 L700 14 C370 92 340 396 140 400 Z" fill="var(--accent-red)"/>
      <path d="M120 400 C350 392 380 80 700 6 L700 12 C390 90 360 396 150 400 Z" fill="#1b1b1c"/>
    </svg>

    <div class="brand">
      <span class="brand-mark"></span>
      <span class="brand-name">Vantorin Kitchens</span>
    </div>

    <p class="holder">MARCUS DELRAY, <span class="holder-role">Director</span></p>
    <p class="address">2180 - 87 Ave. Edmonton<br>AB T5K 2P4</p>

    <ul class="contacts">
      <li>
        <svg class="icon" viewBox="0 0 16 16"><circle cx="8" cy="8" r="7.5" fill="none" stroke="currentColor"/><path d="M5 4 L7 6 L6 7.5 C6.6 8.8 7.3 9.5 8.5 10 L10 9 L12 11 L10.5 12.5 C7 12 4 9 3.5 5.5 Z" fill="currentColor"/></svg>
        780.555.0143
      </li>
      <li>
        <svg class="icon" viewBox="0 0 16 16"><rect x="4" y="2" width="8" height="5" fill="currentColor"/><rect x="1" y="7" width="14" height="6" rx="1" fill="currentColor"/></svg>
        780.555.0187
      </li>
      <li>
        <svg class="icon" viewBox="0 0 16 16"><rect x="4" y="1" width="8" height="14" rx="1.5" fill="currentColor"/><rect x="5.5" y="3" width="5" height="8" fill="var(--panel-grey)"/></svg>
        780.555.0162
      </li>
      <li class="contact-web">vantorinkitchens.ca</li>
    </ul>

    <p class="contact-email">
      <svg class="icon" viewBox="0 0 16 16"><rect x="1" y="3" width="14" height="10" rx="1" fill="currentColor"/><path d="M1.5 4 L8 9 L14.5 4" fill="none" stroke="var(--panel-grey)" stroke-width="1.3"/></svg>
      marcus@vantorinkitchens.ca
    </p>
  </section>

  <section class="card card-back" aria-label="Business card back">
    <div class="back-brand">
      <span class="brand-mark"></span>
      <span class="brand-name">Vantorin Kitchens</span>
    </div>
  </section>

</main>
</body>
</html>
```